Professional Website

We are looking for a new website for our Staffing Company. Attached is a document with all the details and pages needed along with some examples of others websites.

We want a professional Look and feel around the same color theme as the attached Amber Compass.

We currently host our site on PageLoom.io. If the winning designer can also add to PageLoom, that is a plus.

```html
<!DOCTYPE html>
<html lang="en">
<head>
<meta charset="utf-8">
<title>HireNest Clerical &amp; Industrial</title>
<link rel="stylesheet" href="https://fonts.googleapis.com/css2?family=Inter:wght@400;500;600&family=Lato:wght@400;700&family=Catamaran:wght@500;700&display=swap">
<style>
:root{
  --navy:#1d2088;
  --ink-dark:#14163f;
  --nav-bg:rgba(58,62,160,.92);
  --hero-blue:#3d41a6;
  --text:#1a1a1a;
  --muted:#444;
  --white:#fff;
  --line:#333;
  --field:#e6e6e6;
}
*{box-sizing:border-box;margin:0;padding:0}
html,body{width:1200px;height:2726px;overflow:hidden;background:var(--white)}
body{position:relative;font-family:"Lato",sans-serif;color:var(--text)}
.abs{position:absolute}
a{color:inherit;text-decoration:none}

/* top bar */
.topbar{left:0;top:0;width:1200px;height:51px;background:var(--ink-dark);color:var(--white);font:500 17px "Inter",sans-serif}
.topbar .item{position:absolute;top:14px;display:flex;align-items:center;gap:10px}
.topbar .sep{position:absolute;top:16px;opacity:.5;font-size:14px}

/* hero */
.hero{left:0;top:51px;width:1200px;height:600px}
.nav{left:0;top:51px;width:1200px;height:78px;background:var(--nav-bg);color:var(--white);font:500 17px "Inter",sans-serif}
.brand{position:absolute;left:111px;top:18px;display:flex;align-items:center;gap:8px;font:700 32px "Catamaran",sans-serif;color:var(--white);letter-spacing:-.5px}
.brand .dot{width:12px;height:12px;background:var(--white)}
.nav ul{list-style:none}
.nav li{position:absolute;top:28px}
.hero-copy{left:112px;top:246px;color:var(--white);font-family:"Catamaran",sans-serif}
.hero-copy .welcome{font-weight:500;font-size:27px}
.hero-copy h1{font-weight:700;font-size:62px;line-height:61px;margin-top:4px}
.btn-outline,.btn-solid{position:absolute;top:420px;height:59px;display:flex;align-items:center;justify-content:center;font:700 21px "Catamaran",sans-serif}
.btn-outline{left:112px;width:228px;border:2px solid var(--white);color:var(--white)}
.btn-solid{left:371px;width:206px;background:var(--white);color:var(--navy)}

/* jobs */
.section-title{left:0;width:1200px;text-align:center;font:600 42px "Inter",sans-serif;color:var(--ink-dark)}
.rule{left:563px;width:74px;height:4px;background:var(--navy)}
.card{top:882px;width:277px;height:370px;background:var(--white);box-shadow:0 2px 8px rgba(0,0,0,.18);text-align:center}
.card .frame-back{position:absolute;left:48px;top:45px;width:170px;height:165px;border:1.5px solid var(--text)}
.card .frame-front{position:absolute;left:58px;top:35px;width:174px;height:165px;border:4px solid var(--navy);background:var(--white)}
.card .icon-slot{position:absolute;left:40px;top:38px;width:86px;height:86px;background:#dcdde8}
.card h3{position:absolute;left:0;top:225px;width:100%;font:500 21px "Inter",sans-serif}
.card p{position:absolute;left:36px;top:258px;width:205px;font-size:13.5px;line-height:21px;color:var(--muted)}
.card .go{position:absolute;left:131px;top:329px}
.arrow{position:absolute}

/* about */
.about-text{left:180px;top:1593px;width:840px;text-align:center;font:400 17.5px/29px "Inter",sans-serif;color:var(--text)}
.btn-read{left:521px;top:1765px;width:157px;height:58px;background:var(--navy);color:var(--white);display:flex;align-items:center;justify-content:center;font:700 21px "Catamaran",sans-serif}

/* footer */
.footnav{left:0;top:2090px;width:1200px;font:400 18px "Inter",sans-serif;color:var(--text)}
.footnav span{position:absolute}
.foot-logo{left:520px;top:2156px;width:160px;text-align:center;font:700 27px "Catamaran",sans-serif;color:var(--navy);background:var(--white)}
.col{top:2226px;width:300px;text-align:center;font-family:"Inter",sans-serif}
.col h4{font-weight:500;font-size:20px;letter-spacing:.5px;margin-bottom:20px}
.col p{font-size:15.5px;line-height:20px;color:#333}
.socials{display:flex;justify-content:center;gap:22px;margin-top:18px}
.socials i{width:25px;height:25px;border-radius:50%;background:var(--navy)}
.send{display:inline-block;margin-top:16px;font-size:15px;font-weight:500;text-decoration:underline}
.news-title{left:0;top:2450px;width:1200px;text-align:center;font:500 26px "Inter",sans-serif}
.news-sub{left:0;top:2495px;width:1200px;text-align:center;font:400 15px "Inter",sans-serif;color:#555}
.field{left:261px;top:2538px;width:671px;height:65px;border-radius:33px;background:var(--field);box-shadow:0 1px 3px rgba(0,0,0,.2)}
.field span{position:absolute;left:30px;top:22px;font:400 15px "Inter",sans-serif;color:#555}
.btn-sub{left:727px;top:2544px;width:200px;height:53px;border-radius:27px;background:var(--navy);color:var(--white);display:flex;align-items:center;justify-content:center;font:600 15px "Inter",sans-serif}
.legal{top:2657px;font:400 15.5px "Inter",sans-serif}
</style>
</head>
<body>

<!-- top bar -->
<div class="abs topbar">
  <div class="item" style="left:110px">
    <svg width="32" height="32" viewBox="0 0 32 32"><circle cx="16" cy="16" r="14" fill="none" stroke="#fff" stroke-width="2"/><path d="M11 9c1 0 2 3 2 4s-2 1-1 3 3 4 5 5 2-1 3-1 4 1 4 2-2 3-4 3C14 25 7 18 7 12c0-2 3-3 4-3z" fill="#fff"/></svg>
    555-014-2200
  </div>
  <div class="item" style="left:452px">
    <svg width="26" height="26" viewBox="0 0 26 26"><circle cx="13" cy="13" r="11.5" fill="none" stroke="#fff" stroke-width="1.6"/><circle cx="13" cy="10" r="4" fill="none" stroke="#fff" stroke-width="1.6"/><path d="M6 20c2-4 12-4 14 0" fill="none" stroke="#fff" stroke-width="1.6"/></svg>
    Employee Login
  </div>
  <span class="sep" style="left:648px">|</span>
  <div class="item" style="left:693px">
    <svg width="28" height="24" viewBox="0 0 28 24"><rect x="1" y="3" width="26" height="19" rx="2" fill="none" stroke="#fff" stroke-width="1.6"/><circle cx="8" cy="11" r="3" fill="none" stroke="#fff" stroke-width="1.5"/><path d="M3 19c1-3 9-3 10 0M16 9h8M16 13h8M16 17h6" stroke="#fff" stroke-width="1.5" fill="none"/></svg>
    Pay Card Login
  </div>
  <span class="sep" style="left:898px">|</span>
  <div class="item" style="left:936px">
    <svg width="22" height="26" viewBox="0 0 22 26"><path d="M11 1l9 4v7c0 6-4 10-9 13C6 22 2 18 2 12V5z" fill="none" stroke="#fff" stroke-width="1.6"/><circle cx="11" cy="11" r="3" fill="none" stroke="#fff" stroke-width="1.5"/><path d="M6 18c2-3 8-3 10 0" stroke="#fff" stroke-width="1.5" fill="none"/></svg>
    Partner Bank Login
  </div>
</div>

<!-- hero -->
<svg class="abs hero" viewBox="0 51 1200 600" role="img" aria-label="Photo of two smiling young businessmen in suits">
  <defs>
    <linearGradient id="photo" x1="0" y1="0" x2="1" y2="1">
      <stop offset="0" stop-color="#c9cfd8"/><stop offset=".45" stop-color="#a88f7c"/><stop offset="1" stop-color="#2f3a66"/>
    </linearGradient>
    <linearGradient id="blueband" x1="0" y1="0" x2="1" y2="0">
      <stop offset="0" stop-color="#3b3fa4"/><stop offset="1" stop-color="#4b4fb8"/>
    </linearGradient>
  </defs>
  <rect x="0" y="51" width="1200" height="600" fill="url(#photo)"/>
  <polygon points="0,51 600,51 525,390 610,651 0,651" fill="url(#blueband)"/>
  <polygon points="0,51 300,51 0,300" fill="#4448ad" opacity=".7"/>
  <polygon points="400,651 565,390 610,651" fill="#3134a0" opacity=".8"/>
</svg>

<div class="abs nav">
  <div class="brand"><span class="dot"></span>HireNest</div>
  <ul>
    <li style="left:379px">Home</li>
    <li style="left:502px">About</li>
    <li style="left:626px">Jobs</li>
    <li style="left:741px">Testimonial</li>
    <li style="left:908px">Contact us</li>
    <li style="left:1070px;top:27px"><svg width="18" height="18" viewBox="0 0 18 18"><circle cx="7.5" cy="7.5" r="5.5" fill="none" stroke="#fff" stroke-width="2"/><path d="M11.5 11.5L16 16" stroke="#fff" stroke-width="2"/></svg></li>
  </ul>
</div>

<div class="abs hero-copy">
  <div class="welcome">Welcome To</div>
  <h1>HireNest Clerical<br>&amp; Industrial</h1>
</div>
<a class="btn-outline" href="#">I’m looking for a Job</a>
<a class="btn-solid" href="#">I need Employees</a>

<!-- jobs panel -->
<h2 class="abs section-title" style="top:744px">Jobs Panel</h2>
<div class="abs rule" style="top:812px"></div>

<svg class="arrow" style="left:44px;top:1025px" width="29" height="29" viewBox="0 0 28 28"><circle cx="14" cy="14" r="14" fill="#111"/><path d="M20 14H9M13 9l-5 5 5 5" stroke="#fff" stroke-width="3" fill="none"/></svg>
<svg class="arrow" style="left:1124px;top:1043px" width="29" height="29" viewBox="0 0 28 28"><circle cx="14" cy="14" r="14" fill="#111"/><path d="M8 14h11M15 9l5 5-5 5" stroke="#fff" stroke-width="3" fill="none"/></svg>

<div class="abs card" style="left:111px">
  <div class="frame-back"></div>
  <div class="frame-front"><div class="icon-slot" role="img" aria-label="Welder icon"></div></div>
  <h3>Welders</h3>
  <p>We are hiring for, a reputed metal display company located in Hammond, IN...</p>
  <svg class="go" width="16" height="16" viewBox="0 0 16 16"><circle cx="8" cy="8" r="8" fill="#111"/><path d="M4 8h7M8 5l3 3-3 3" stroke="#fff" stroke-width="2" fill="none"/></svg>
</div>
<div class="abs card" style="left:461px">
  <div class="frame-back"></div>
  <div class="frame-front"><div class="icon-slot" role="img" aria-label="Forklift icon"></div></div>
  <h3>Material Handlers</h3>
  <p>We are hiring for, a reputed metal display company located in Hammond, IN...</p>
  <svg class="go" width="16" height="16" viewBox="0 0 16 16"><circle cx="8" cy="8" r="8" fill="#111"/><path d="M4 8h7M8 5l3 3-3 3" stroke="#fff" stroke-width="2" fill="none"/></svg>
</div>
<div class="abs card" style="left:810px">
  <div class="frame-back"></div>
  <div class="frame-front"><div class="icon-slot" role="img" aria-label="Construction worker icon"></div></div>
  <h3>General Labour</h3>
  <p>We are hiring for, a reputed metal display company located in Hammond, IN...</p>
  <svg class="go" width="16" height="16" viewBox="0 0 16 16"><circle cx="8" cy="8" r="8" fill="#111"/><path d="M4 8h7M8 5l3 3-3 3" stroke="#fff" stroke-width="2" fill="none"/></svg>
</div>

<!-- about band -->
<svg class="abs" style="left:0;top:1300px" width="1200" height="760" viewBox="0 1300 1200 760">
  <defs>
    <linearGradient id="panel" x1="0" y1="0" x2="0" y2="1">
      <stop offset="0" stop-color="#f1f1f3"/><stop offset=".25" stop-color="#fff"/><stop offset=".8" stop-color="#fff"/><stop offset="1" stop-color="#ececee"/>
    </linearGradient>
  </defs>
  <polygon points="0,1450 1200,1313 1200,1885 0,1995" fill="url(#panel)"/>
  <polygon points="0,1310 410,1403 0,1450" fill="var(--navy)"/>
  <polygon points="820,1920 1200,1885 1200,2045" fill="var(--navy)"/>
</svg>

<h2 class="abs section-title" style="top:1497px">About HireNest</h2>
<div class="abs rule" style="top:1565px"></div>
<p class="abs about-text">Greatest part of our daily job is that we are constantly bringing people together.<br>Our Clients come to us in search of the perfect candidate and the job hunters approach us when they are in need of a job or looking for their next exciting role.Being able to work with and connect the two is incredibly satisfying. Not to mention that in today's current job market, employers are fighting for the top talent. This makes our employees and partners grateful for the help in finding it!</p>
<a class="abs btn-read" href="#">Read More</a>

<!-- footer -->
<nav class="abs footnav">
  <span style="left:194px">Home</span><span style="left:285px">•</span>
  <span style="left:331px">Job</span><span style="left:401px">•</span>
  <span style="left:440px">Enroll For Free</span><span style="left:606px">•</span>
  <span style="left:645px">About</span><span style="left:739px">•</span>
  <span style="left:774px">Articles</span><span style="left:875px">•</span>
  <span style="left:916px">Contact us</span>
</nav>

<svg class="abs" style="left:0;top:2170px" width="1200" height="240" viewBox="0 2170 1200 240">
  <path d="M108 2173H520M688 2173H1085M432 2173V2403M767 2173V2403" stroke="var(--line)" stroke-width="1"/>
</svg>
<div class="abs foot-logo">HireNest</div>

<div class="abs col" style="left:125px">
  <h4>GET SOCIAL</h4>
  <p style="font-size:17px;color:#555">Follow us on social networks</p>
  <div class="socials"><i></i><i></i><i></i><i></i></div>
</div>
<div class="abs col" style="left:446px">
  <h4>WE ARE HERE</h4>
  <p>PO Box 420<br>Riverton, CA 95410,USA</p>
  <p style="margin-top:12px">hello@hirenest.com</p>
  <p style="margin-top:12px">555-014-2200</p>
</div>
<div class="abs col" style="left:777px">
  <h4>LET’S TALK</h4>
  <p style="font-size:17px">Here a questions or just want<br>to say hello?</p>
  <a class="send" href="#">SEND US MESSAGE</a>
</div>

<div class="abs news-title">SIGN UP FOR NEWSLETTER</div>
<div class="abs news-sub">we’re open! sign up for <b style="color:#222;font-weight:600">hirenest</b> news &amp; updates</div>
<div class="abs field"><span>Enter Email</span></div>
<a class="abs btn-sub" href="#">SUBSCRIBE NOW</a>

<div class="abs legal" style="left:108px">Copyrights@2022.hirenest.com All Rights Reserved</div>
<div class="abs legal" style="left:796px">Privacy Policy &nbsp;&nbsp; | &nbsp;&nbsp; Terms &amp; Conditions</div>

</body>
</html>
```